Eyecatching website design for commercial lighting business

This contest is all about the graphic design aspect. We need a striking website design for a commercial lighting company. We want something really eye catching to introduce people to our range of induction and LED lights which save businesses money on maintenance and electricity costs.

To be successful in this contest you will need to provide a design and pictures for the pages listed below.

We are using the platform velbrin.com.au and you can see the attached template which everything will be loaded into so we just need HTML files which we can upload and we can do everything else from Velbrin.

The final design should be strong and clean and use the colours and textures in the attached business card file.

Detailed requirements:

Please see attached screenshot of the website template, all we need is a fantastic graphic design and improvement/ incorporation of our logo for the following pages
Page Headings:
1. Home
About Us, Contact Us, snapshot of and link to Blog

Each of the below pages will have several paragraphs of text followed by a list of suitable products which is generated from our product catalogue.

2. Car Park Lighting
3. Educational Lighting
4. Hospitality Lighting
5. Office & Shop Lighting
6. Warehouse Lighting

Some of the website we have seen which are similar in nature are:
http://www.quorvanlamps.com.au/
http://www.tibrox.com/
http://www.gandowlumen.net/commercial-led
but we really want a modern, eye catching and memorable design

Some of the designs built on Velbrin that we like are:

http://www.pemberhollow.com.au/
http://www.marwickgoods.com.au/
http://www.kelmorabay.com.au/

I've also uploaded a couple of photos that we love. We'd like something similar for each industry.

Target Market(s)

Company Owners, Maintenance & Facilities Managers, Electrical Contractors

Industry/Entity Type

Electrical

Coding

Coded - Design and coding required

Number of Pages Required

5+ page

Font styles to use
Sans Serif

Colors
33a6d7
ec1f27

Requirements
Must have
• -Must scale to mobile
• -HTML coded files need to be provided (HTML Bootstrap)
Nice to have
• -Prefer incorporation of our logo into header bar
• -Design of 2-3 advertising banners which can be displayed on the home page
• -Prominent call to action button towards top of page 'Get a quote' or similar
• -Grid based design HTML Bootstrap

```html
<!DOCTYPE html>
<html lang="en">
<head>
<meta charset="utf-8">
<title>Halvern Commercial Lighting</title>
<link href="https://fonts.googleapis.com/css2?family=Open+Sans:wght@400;600;700;800&display=swap" rel="stylesheet">
<style>
  :root{
    --red:#d61f27;
    --red-deep:#a3151b;
    --blue:#33a6d7;
    --dark:#1b1b1d;
    --darker:#111113;
    --grey-card:#e4e4e4;
    --text:#333;
    --muted:#777;
    --white:#fff;
  }
  *{box-sizing:border-box;margin:0;padding:0}
  html,body{width:1200px;height:2760px;overflow:hidden}
  body{font-family:"Open Sans",Arial,sans-serif;color:var(--text);background:var(--white);position:relative}

  /* header */
  .site-header{position:absolute;top:0;left:0;width:1200px;height:140px;
    background:repeating-linear-gradient(45deg,#2a2a2c 0 3px,#222224 3px 6px);
    display:flex;align-items:center;justify-content:space-between;padding:0 40px}
  .brand-name{font-weight:700;font-size:24px;color:var(--white);letter-spacing:.5px}
  .main-nav{display:flex;gap:28px}
  .main-nav a{color:var(--white);text-decoration:none;font-size:15px;font-weight:700;text-transform:uppercase}

  /* hero */
  .hero{position:absolute;top:140px;left:0;width:1200px;height:572px;background:#2a0c0f;overflow:hidden}
  .hero-photo{position:absolute;inset:0;
    background:radial-gradient(circle at 28% 52%,#ffd7dc 0,#ff5a6a 12%,#c3142a 30%,#5a0b12 55%,#1c0a0c 80%)}
  .hero-copy{position:absolute;right:40px;top:130px;width:560px;color:var(--white);text-align:right}
  .hero-copy h1{font-size:29px;font-weight:700;line-height:1.3;text-transform:uppercase}
  .hero-copy p{font-size:15px;line-height:1.55;margin-top:16px}
  .btn-outline{display:inline-block;margin-top:26px;border:2px solid var(--white);color:var(--white);
    padding:10px 22px;font-size:15px;font-weight:600;text-transform:uppercase}
  .slider-dots{position:absolute;bottom:26px;left:50%;transform:translateX(-50%);display:flex;gap:10px}
  .slider-dots span{width:11px;height:11px;border-radius:50%;background:#fff;opacity:.8}

  /* section titles */
  .section-title{font-size:28px;font-weight:700;text-transform:uppercase;color:#444}
  .section-title em{font-style:normal;color:var(--red)}

  /* solutions */
  .solutions{position:absolute;top:712px;left:0;width:1200px;height:488px;background:var(--white);padding:80px 100px 0}
  .solution-grid{display:flex;gap:24px;margin-top:26px}
  .solution-card{width:232px;background:var(--grey-card);text-align:center;padding-bottom:14px}
  .solution-card .photo{height:188px}
  .solution-card h3{font-size:14px;font-weight:700;margin-top:12px;text-transform:uppercase;color:#222}
  .solution-card p{font-size:11px;color:var(--muted);margin-top:4px}

  /* blog */
  .blog{position:absolute;top:1200px;left:0;width:1200px;height:520px;
    background:linear-gradient(#141416,#232326);padding-top:70px}
  .blog .section-title{color:var(--white);text-align:center}
  .blog-grid{display:flex;gap:40px;justify-content:center;margin-top:34px}
  .blog-card{width:480px;color:var(--white)}
  .blog-card .photo{height:200px}
  .blog-card h3{color:var(--red);font-size:12px;font-weight:700;margin-top:14px;text-transform:uppercase}
  .blog-card p{font-size:11px;line-height:1.5;margin-top:4px;text-transform:uppercase;color:#ddd}
  .btn-red{display:inline-block;background:var(--red);color:var(--white);font-size:11px;font-weight:600;
    padding:7px 14px;margin-top:14px;text-transform:uppercase}

  /* video */
  .video{position:absolute;top:1720px;left:0;width:1200px;height:520px;background:var(--white);text-align:center;padding-top:30px}
  .video-frame{position:relative;width:840px;height:380px;margin:28px auto 0;background:#0b1420}
  .video-frame .photo{position:absolute;inset:0 0 36px 0}
  .video-bar{position:absolute;left:0;right:0;bottom:0;height:36px;background:#111;display:flex;align-items:center;padding:0 14px;gap:12px}
  .video-progress{flex:1;height:4px;background:#555}
  .video-progress span{display:block;width:18%;height:100%;background:var(--red)}

  /* footer */
  .site-footer{position:absolute;top:2240px;left:0;width:1200px;height:360px;background:var(--red-deep);color:var(--white);
    display:flex;gap:80px;padding:30px 60px 0}
  .footer-col h4{font-size:20px;font-weight:700;text-transform:uppercase;margin-bottom:14px}
  .about{width:560px}
  .about p{font-size:13px;line-height:1.55}
  .about-body{display:flex;gap:20px;margin-top:20px}
  .about ul{list-style:none;width:390px}
  .about li{font-size:11px;line-height:1.5;margin-bottom:12px;display:flex;gap:8px}
  .about li svg{flex:none;margin-top:3px}
  .about .photo{width:160px;height:150px;border:4px solid var(--white)}
  .newsletter{width:420px}
  .newsletter p{font-size:12px}
  .subscribe{display:flex;margin-top:14px;width:380px}
  .subscribe span{flex:1;background:var(--white);color:#999;font-size:12px;padding:10px}
  .subscribe b{background:#1e1e1e;font-size:12px;padding:10px 16px}
  .newsletter small{display:block;font-size:10px;margin-top:6px;opacity:.85}
  .follow{margin-top:28px}
  .socials{display:flex;gap:8px;margin-top:8px}
  .socials span{width:26px;height:26px;border-radius:50%;background:var(--blue)}
  .socials span:nth-child(3),.socials span:nth-child(5){background:#e44}

  .bottom-bar{position:absolute;top:2600px;left:0;width:1200px;height:160px;background:var(--darker);color:#ccc;padding:40px 60px}
  .bottom-bar nav{display:flex;gap:20px;font-size:12px;text-transform:uppercase}
  .bottom-bar p{font-size:11px;margin-top:14px}
</style>
</head>
<body>

<header class="site-header">
  <div class="brand"><span class="brand-name">Halvern Commercial Lighting</span></div>
  <nav class="main-nav"><a>Home</a><a>About Us</a><a>Products</a><a>Blog</a><a>Contact Us</a></nav>
</header>

<section class="hero">
  <div class="hero-photo" role="img" aria-label="Close-up of a glowing red LED lamp"></div>
  <div class="hero-copy">
    <h1>Welcome to the Commercial Lighting Division of Halvern</h1>
    <p>Retrofitting the lighting in a commercial or industrial premises is a great way to save money on energy costs and maintenance, create a safer work environment and reduce the load on the wiring in the premises.</p>
    <span class="btn-outline">Read More</span>
  </div>
  <div class="slider-dots"><span></span><span></span><span></span></div>
</section>

<section class="solutions">
  <h2 class="section-title">Lighting <em>Solutions</em></h2>
  <div class="solution-grid">
    <article class="solution-card"><div class="photo" role="img" aria-label="Lit underground car park" style="background:linear-gradient(#c9ccd0,#6d7278)"></div><h3>Car Park Lighting</h3><p>Bright, safe parking areas</p></article>
    <article class="solution-card"><div class="photo" role="img" aria-label="Classroom with ceiling lights" style="background:linear-gradient(#e8e9ea,#9ea4aa)"></div><h3>Educational Lighting</h3><p>Clear light for learning</p></article>
    <article class="solution-card"><div class="photo" role="img" aria-label="Colourful hospitality venue lights" style="background:linear-gradient(135deg,#d9a34a,#6f9fd0,#c45aa4)"></div><h3>Hospitality Lighting</h3><p>Warm light for venues</p></article>
    <article class="solution-card"><div class="photo" role="img" aria-label="Open-plan office with blue seating" style="background:linear-gradient(#e6eef4,#3d7fb8)"></div><h3>Office Lighting</h3><p>Efficient light for workspaces</p></article>
  </div>
</section>

<section class="blog">
  <h2 class="section-title">Blog Post</h2>
  <div class="blog-grid">
    <article class="blog-card">
      <div class="photo" role="img" aria-label="Row of glowing light bulbs on a blue background" style="background:linear-gradient(#0c4f9c,#2aa3e0)"></div>
      <h3>Saving energy with LED</h3>
      <p>Switching to modern LED fittings cuts power use and upkeep for busy sites. Find out how a simple retrofit can pay for itself within a few short years while giving staff and visitors brighter, safer spaces to work in every day.</p>
      <span class="btn-red">Read More</span>
    </article>
    <article class="blog-card">
      <div class="photo" role="img" aria-label="Single bulb against an orange background" style="background:linear-gradient(90deg,#d86a0c,#f5a623)"></div>
      <h3>Why choose induction lights</h3>
      <p>Induction lamps last for many years with very little care, making them ideal for high ceilings and hard to reach places. Learn where they work best and how they compare with other options across warehouses, car parks and halls.</p>
      <span class="btn-red">Read More</span>
    </article>
  </div>
</section>

<section class="video">
  <h2 class="section-title">Our <em>Video</em></h2>
  <div class="video-frame">
    <div class="photo" role="img" aria-label="Floodlit tennis courts at night with a street light fixture" style="background:linear-gradient(#1a2a44,#33465e 60%,#1e3a2c)"></div>
    <div class="video-bar">
      <svg width="14" height="14" viewBox="0 0 14 14"><path d="M2 1l11 6-11 6z" fill="#fff"/></svg>
      <div class="video-progress"><span></span></div>
    </div>
  </div>
</section>

<footer class="site-footer">
  <div class="footer-col about">
    <h4>About Us</h4>
    <p>Retrofitting the lighting in a commercial or industrial premises is a great way to save money on energy costs and maintenance, create a safer work environment and reduce the load on the wiring in the premises.</p>
    <div class="about-body">
      <ul>
        <li><svg width="12" height="12" viewBox="0 0 12 12"><path d="M1 6l3 3 7-7" stroke="#fff" stroke-width="2" fill="none"/></svg>The best range of energy saving commercial &amp; industrial lighting</li>
        <li><svg width="12" height="12" viewBox="0 0 12 12"><path d="M1 6l3 3 7-7" stroke="#fff" stroke-width="2" fill="none"/></svg>High quality products from reputable manufacturers which meet Australian Standards</li>
        <li><svg width="12" height="12" viewBox="0 0 12 12"><path d="M1 6l3 3 7-7" stroke="#fff" stroke-width="2" fill="none"/></svg>Assistance to ensure you receive the right product for the right application</li>
      </ul>
      <div class="photo" role="img" aria-label="Industrial high bay light fitting" style="background:linear-gradient(#f2f2f2,#b8a98a)"></div>
    </div>
  </div>
  <div class="footer-col newsletter">
    <h4>Newsletter Sign Up</h4>
    <p>Get the latest news updates of us, subscribe below.</p>
    <div class="subscribe"><span>Enter your email here</span><b>SEARCH</b></div>
    <small>We never share your email address with others</small>
    <div class="follow"><p>Follow us</p>
      <div class="socials"><span></span><span></span><span></span><span></span><span></span></div>
    </div>
  </div>
</footer>

<div class="bottom-bar">
  <nav><span>Home</span><span>About Us</span><span>Products</span><span>Blog</span><span>Contact Us</span></nav>
  <p>COPYRIGHT © 2014 HALVERN COMMERCIAL LIGHTING. ALL RIGHTS RESERVED.</p>
</div>

</body>
</html>
```